IT support company needs Banner Ad for the top of their quote layout template

We need a banner Ad for the top of our for quote layout template so it is sent out on all our quotes

The banner size must be 827 x 100 pixels - anything larger than 60 KB can cause upload time issues

We have attached our logo and examples of the quote page to see how it looks in the context of the whole page.

Essential elements of the banner
- Must have our logo but this can be changed to be different colours if it makes the design work better i.e. Kelmor Wave could be all in white

Colours
- Can use all of our standard colours - Orange, Black, Grey and White

Images
- As a premium IT support company we deal with people and technology so would like to see both of these Incorporated into the banner i.e. people using technology These images could be watermarked or one colour effect.

Look and Feel
- Professional, friendly, people, technology, premium

Target Market
Small business owners and managers

Industry/Entity Type

It Company

```html
<!DOCTYPE html>
<html lang="nl">
<head>
<meta charset="utf-8">
<title>Offerte DJ-000280</title>
<link href="https://fonts.googleapis.com/css2?family=Carlito:wght@400;700&display=swap" rel="stylesheet">
<style>
:root{
  --orange:#e8591a;
  --orange-mid:#f07a30;
  --ink:#111;
  --grey:#8a8a8a;
  --stripe:#f2f2f2;
  --white:#fff;
}
*{box-sizing:border-box;margin:0;padding:0}
html,body{width:891px;height:1200px;overflow:hidden;background:var(--white)}
body{position:relative;font-family:"Carlito",Calibri,sans-serif;color:var(--ink);font-size:14.5px}
.abs{position:absolute}

.banner{left:0;top:0;width:891px;height:105px;background:linear-gradient(90deg,var(--orange) 0%,var(--orange-mid) 40%,var(--orange) 100%)}
.banner-art{left:300px;top:0;width:380px;height:105px;background:radial-gradient(ellipse at 55% 60%,rgba(255,190,130,.55) 0%,rgba(255,170,100,.25) 45%,rgba(232,89,26,0) 75%)}
.banner-rule{left:0;top:108px;width:891px;height:5px;background:var(--orange)}
.brand{left:32px;top:36px;color:var(--white);font-weight:700;font-size:38px;letter-spacing:1px;line-height:1}
.banner-contact{right:29px;top:20px;text-align:right;color:var(--white);font-weight:700;font-size:13.5px;line-height:17px}

.doc-title{left:28px;top:150px;font-size:22px;font-weight:400}
.photo{left:28px;top:192px;width:106px;height:140px;background:linear-gradient(160deg,#c9c2b8,#5b5b5e)}
.party{top:190px;line-height:18.5px}
.party h3{color:var(--orange);font-weight:400;font-size:17.5px;margin-bottom:3px}
.party b{font-weight:700}
.party.from{left:145px}
.party.to{left:388px}
.party.meta{left:675px}
.party.meta .gap{margin-top:2px}
.divider{left:27px;top:344px;width:835px;height:3px;background:var(--orange)}

.section-title{left:28px;font-size:19.5px;font-weight:400}
.table{left:27px;width:835px;border-collapse:collapse;border:1.5px solid var(--ink)}
.table th{background:var(--orange);color:var(--white);font-weight:400;height:27px;text-align:left;padding:0 6px;font-size:14.5px}
.table th.num{width:117px;text-align:right}
.table td{height:28px;padding:0 6px}
.table .num{text-align:right;border-left:1.5px solid var(--ink)}
.table tr.alt td{background:var(--stripe)}
.totals{width:835px;left:27px;font-size:14.5px}
.totals div{display:flex;justify-content:flex-end;height:27px;align-items:center}
.totals span{color:var(--grey)}
.totals b{width:116px;text-align:right;padding-right:5px}

.terms{left:28px;top:994px;font-size:14px}
.sign-line{top:1071px;height:1.5px;background:var(--ink)}
.sign-label{top:1074px;font-size:14px}

.footer{left:0;top:1153px;width:891px;height:47px;background:var(--orange)}
.footer::before{content:"";position:absolute;left:0;top:6px;width:100%;height:2px;background:var(--white)}
.footer-text{top:1170px;color:var(--white);font-size:14.5px}
</style>
</head>
<body>
<header>
  <div class="abs banner"></div>
  <div class="abs banner-art" role="img" aria-label="Faint silhouettes of business people before a globe"></div>
  <div class="abs banner-rule"></div>
  <div class="abs brand">KELMOR WAVE</div>
  <div class="abs banner-contact">Alder House, Greenways, Marsh Lane<br>Eastbrook, Norfolk, NR99 4XQ<br>www.kelmorwave.co.uk<br>01632 960482</div>
</header>

<h1 class="abs doc-title">Standard MSP&nbsp; #2</h1>
<div class="abs photo" role="img" aria-label="Portrait photo of the account manager"></div>

<div class="abs party from">
  <h3>Opgesteld door:</h3>
  <b>Owen Marsh Ltd</b><br>Owen Marsh<br><br>Fax<br>owen.marsh@quotora.com
</div>
<div class="abs party to">
  <h3>Opgesteld voor:</h3>
  <b>Red Canyon</b><br>2817 Hollis Rd.<br>Tulsa,&nbsp;&nbsp; 74190<br>Rosalind Pierce<br>nora.webb@bluefinch.co.uk
</div>
<div class="abs party meta">
  <h3>Gegevens Offerte:</h3>
  <b>Offerte #: DJ-000280</b><br>Versie: 1<br><div class="gap">Leverdatum: 14/11/2017<br>Vervaldatum: 31/12/2017</div>
</div>
<div class="abs divider"></div>

<h2 class="abs section-title" style="top:365px">Overzicht Offerte</h2>
<table class="abs table" style="top:396px">
  <tr><th>Beschrijving</th><th class="num">Bedrag</th></tr>
  <tr><td>Initial Investment</td><td class="num">$800.00</td></tr>
</table>
<div class="abs totals" style="top:454px">
  <div><span>Subtotaal:</span><b>$800.00</b></div>
  <div><span>VAT:</span><b>$160.00</b></div>
  <div><span>Totaal:</span><b>$960.00</b></div>
</div>

<h2 class="abs section-title" style="top:555px">Overzicht Terugkerende Kosten</h2>
<table class="abs table" style="top:585px">
  <tr><th>Beschrijving</th><th class="num">Bedrag</th></tr>
  <tr><td>Monitoring</td><td class="num">$375.00</td></tr>
  <tr class="alt"><td>Support</td><td class="num">$65.00</td></tr>
  <tr><td>Fixed Hours</td><td class="num">$850.00</td></tr>
</table>
<div class="abs totals" style="top:700px">
  <div><span>Terugkerende totaal:</span><b>$1,290.00</b></div>
</div>

<h2 class="abs section-title" style="top:747px">*Optionele kosten</h2>
<table class="abs table" style="top:778px">
  <tr><th>Beschrijving</th><th class="num">Recurring</th><th class="num">One-Time</th></tr>
  <tr><td>Monitoring</td><td class="num">$790.00</td><td class="num">$0.00</td></tr>
  <tr class="alt"><td>Support</td><td class="num">$185.00</td><td class="num">$0.00</td></tr>
  <tr><td>Fixed Hours</td><td class="num">$695.00</td><td class="num">$0.00</td></tr>
  <tr class="alt"><td>Add-on Services</td><td class="num">$850.00</td><td class="num">$0.00</td></tr>
</table>
<div class="abs totals" style="top:921px">
  <div><span>Optionele terugkerend bedrag:</span><b>$2,520.00</b></div>
  <div><span>Optionele ongeplande Subtotaal:</span><b>$.00</b></div>
</div>

<p class="abs terms">Taxes, shipping, handling and other fees may apply.&nbsp; We reserve the right to cancel orders arising from pricing or other errors.</p>

<div class="abs sign-line" style="left:27px;width:500px"></div>
<div class="abs sign-line" style="left:558px;width:196px"></div>
<div class="abs sign-label" style="left:28px">Handtekening</div>
<div class="abs sign-label" style="left:560px">Datum</div>

<footer>
  <div class="abs footer"></div>
  <div class="abs footer-text" style="left:28px">Offerte #DJ-000280 v1</div>
  <div class="abs footer-text" style="right:31px">Pagina 6 Van 7</div>
</footer>
</body>
</html>
```